Brimsett Gardening Fresh New Website

We are looking to create a simple fresh website for our landscaping business. The website should appeal to a 'high end' audience. We deal with a lot of Embassies and affluent clients who have extremely large gardens that are meticulously maintained. The site is about communicating our excellent landscaping and customer service skills and encouraging new clients to reach out and engage us to take care of their gardens.

The website is basically going to be our business card, it will have almost no functionality other than two 'contact us' forms, one for smaller clients and one for more detailed projects.

The website will not have a lot of written content and will have to show photos of beautifully landscaped gardens.

The main logo in black will influence the site, however, we are open to all suggestions.

We are expecting to have the following pages:
Home Page
Services
About Us
Contact Us
Showcase (photo gallery of our work)

We need someone who can code it to wordpress and be available for minor changes over a number of days. They will be simple tweaks.

```html
<!DOCTYPE html>
<html lang="en">
<head>
<meta charset="utf-8">
<title>Brimsett Gardening – Landscaping &amp; Lawn Care</title>
<link rel="stylesheet" href="https://fonts.googleapis.com/css2?family=Gelasio:wght@600;700&family=Poppins:wght@400;500;600;700&display=swap">
<style>
:root{
  --gold:#b8892b;
  --gold-dark:#a2741c;
  --gold-light:#f4d24a;
  --gold-grad:linear-gradient(90deg,#a87a22 0%,#f4d24a 100%);
  --ink:#111111;
  --text:#2b2b2b;
  --muted:#f3f3f3;
  --white:#ffffff;
  --footer:#0d0d0d;
}
*{box-sizing:border-box;margin:0;padding:0}
html,body{width:1200px;height:4194px;overflow:hidden}
body{font-family:"Poppins",Arial,sans-serif;color:var(--text);background:var(--white);position:relative}
.abs{position:absolute}
.heading{font-family:"Gelasio",Georgia,serif;font-weight:700;color:var(--ink);text-align:center;font-size:37px;line-height:1}
.heading .accent{color:var(--gold)}
.btn{position:absolute;display:flex;align-items:center;justify-content:center;background:var(--gold-grad);color:var(--ink);font-weight:600;font-size:12px}
p{font-size:11px;line-height:22.5px}

/* Hero */
.hero{position:absolute;left:0;top:0;width:1200px;height:589px;overflow:hidden}
.hero-photo{position:absolute;inset:0;background:radial-gradient(ellipse at 50% 45%,#8d8f86 0%,#5c6a4c 30%,#2f4a24 65%,#1d2f17 100%)}
.hero-shade{position:absolute;inset:0;background:rgba(0,0,0,.18)}
.nav-line{position:absolute;left:0;width:1200px;height:2px;background:var(--gold)}
.nav-link{position:absolute;top:69px;color:var(--white);font-size:14px;font-weight:500;transform:translateX(-50%)}
.brand-badge{position:absolute;left:552px;top:20px;width:120px;height:120px;border-radius:50%;background:#0f0f0f;border:2px solid var(--gold);display:flex;flex-direction:column;align-items:center;justify-content:center;color:var(--gold);font-size:11px;font-weight:500;letter-spacing:2px;text-align:center;line-height:16px}
.nav-contact{left:959px;top:62px;width:111px;height:36px;border-radius:18px;font-size:11px;color:var(--white);text-transform:uppercase}
.hero-title{position:absolute;left:0;top:246px;width:1200px;text-align:center;color:var(--white);font-weight:700;font-size:47px;line-height:54px;text-transform:uppercase}
.hero-btn{left:545px;top:428px;width:110px;height:39px;border-radius:20px;background:#b98a2e;color:var(--white);font-size:11px;text-transform:uppercase}
.scroll-badge{position:absolute;left:567px;top:556px;width:66px;height:66px;border-radius:50%;background:var(--white);box-shadow:0 4px 12px rgba(0,0,0,.2);display:flex;align-items:center;justify-content:center}

/* Services */
.service-card{position:absolute;top:775px;width:291px;height:313px;background:var(--white);box-shadow:0 10px 24px rgba(0,0,0,.09);text-align:center}
.service-photo{height:172px}
.service-icon{position:absolute;left:108px;top:134px;width:75px;height:75px;border-radius:50%;background:var(--white);display:flex;align-items:center;justify-content:center}
.service-title{position:absolute;top:200px;left:0;width:100%;font-family:"Gelasio",Georgia,serif;font-weight:700;font-size:17px;color:var(--ink)}
.service-text{position:absolute;top:230px;left:16px;right:16px;font-size:11px;line-height:22.5px}

/* About */
.about{position:absolute;left:0;top:1245px;width:1200px;height:508px;background:var(--muted)}
.about-title{position:absolute;left:142px;top:100px;font-family:"Gelasio",Georgia,serif;font-weight:700;font-size:38px;line-height:46px;color:var(--ink)}
.about-title .accent{color:var(--gold)}
.about-text{position:absolute;left:142px;top:193px;width:460px}
.about-text p{margin-bottom:7px}
.about-frame{position:absolute;left:659px;top:85px;width:399px;height:322px;border:3px solid var(--gold-dark);border-left:none;border-bottom:none}
.about-frame::after{content:"";position:absolute;right:-3px;bottom:0;width:3px;height:100%;background:var(--gold-dark)}
.about-photo{position:absolute;left:646px;top:98px;width:398px;height:324px;background:linear-gradient(180deg,#c8d6e2 0%,#dfe4e6 45%,#7e9e4a 72%,#5f8a2e 100%)}

/* Reviews */
.review-card{position:absolute;left:283px;top:1934px;width:634px;height:183px;background:var(--white);box-shadow:0 10px 24px rgba(0,0,0,.08);text-align:center}
.quote-badge{position:absolute;left:563px;top:1903px;width:58px;height:58px;border-radius:50%;background:var(--gold-grad);display:flex;align-items:center;justify-content:center;font-family:"Gelasio",Georgia,serif;font-size:44px;font-weight:700;color:var(--ink);line-height:1;padding-top:22px}
.review-text{position:absolute;left:50px;right:50px;top:40px}
.review-name{position:absolute;left:0;width:100%;top:112px;font-size:13px;font-weight:500;color:var(--ink)}
.review-arrows{position:absolute;left:292px;top:140px}

/* Band */
.band{position:absolute;left:0;top:2219px;width:1200px;height:430px;overflow:hidden}
.band-photo{position:absolute;inset:0;background:linear-gradient(180deg,#4c5a45 0%,#5e5c52 45%,#3f3d38 100%)}
.band-shade{position:absolute;inset:0;background:rgba(20,20,20,.45)}
.band-title{position:absolute;left:0;width:1200px;top:137px;text-align:center;font-family:"Gelasio",Georgia,serif;font-weight:700;font-size:37px;color:var(--white)}
.band-text{position:absolute;left:200px;width:800px;top:191px;text-align:center;color:var(--white)}

/* Gallery */
.gallery-tile{position:absolute;width:292px;height:218px}
.gallery-caption{position:absolute;inset:0;background:rgba(25,25,22,.55);color:var(--white);text-align:center;padding:44px 18px 0}
.gallery-caption h3{font-family:"Gelasio",Georgia,serif;font-weight:700;font-size:18px;margin-bottom:10px}

/* Inquiry */
.inquiry{position:absolute;left:0;top:3399px;width:1200px;height:467px;background:var(--muted)}
.field{position:absolute;background:var(--white);font-size:12px;color:var(--ink);padding:8px 18px}

/* Footer */
.footer{position:absolute;left:0;top:3866px;width:1200px;height:294px;background:var(--footer);color:var(--white)}
.footer-brand{position:absolute;left:142px;top:80px;width:150px;text-align:center;color:var(--gold);font-size:18px;font-weight:500;letter-spacing:4px;line-height:26px}
.footer-head{position:absolute;top:66px;font-size:13px;font-weight:500}
.footer-links{position:absolute;left:413px;top:96px;list-style:none;font-size:11px;line-height:25.5px}
.contact-row,.social-row{position:absolute;display:flex;align-items:center;font-size:11.5px;line-height:15px}
.icon-dot{width:36px;height:36px;border-radius:50%;background:var(--gold-grad);margin-right:14px;display:flex;align-items:center;justify-content:center;flex:none}
.copyright{position:absolute;left:0;top:4160px;width:1200px;height:34px;background:var(--gold-grad);display:flex;align-items:center;justify-content:center;font-size:12px;color:var(--ink)}
</style>
</head>
<body>

<header class="hero">
  <div class="hero-photo" role="img" aria-label="Formal garden with stone gazebo, clipped shrubs and circular paved path"></div>
  <div class="hero-shade"></div>
  <div class="nav-line" style="top:48px"></div>
  <div class="nav-line" style="top:110px"></div>
  <a class="nav-link" style="left:174px">Home</a>
  <a class="nav-link" style="left:306px">About Us</a>
  <a class="nav-link" style="left:451px">Services</a>
  <a class="nav-link" style="left:778px">Our Gallery</a>
  <div class="brand-badge">BRIMSETT<br>GARDENING</div>
  <a class="btn nav-contact">Contact Us</a>
  <h1 class="hero-title">Brimsett Gardening<br>Your Full Landscaping &amp;<br>Lawn Care Experts</h1>
  <a class="btn hero-btn">Read More</a>
</header>
<div class="scroll-badge">
  <svg width="22" height="36" viewBox="0 0 22 36"><rect x="2" y="2" width="18" height="32" rx="9" fill="none" stroke="#111" stroke-width="2"/><line x1="11" y1="8" x2="11" y2="14" stroke="#111" stroke-width="2" stroke-linecap="round"/></svg>
</div>

<h2 class="heading abs" style="left:0;width:1200px;top:706px">Our <span class="accent">Services</span></h2>

<article class="service-card" style="left:142px">
  <div class="service-photo" role="img" aria-label="Green lawn bordered by flowering shrubs" style="background:linear-gradient(180deg,#c24a3a 0%,#7aa63b 45%,#3f9a2a 100%)"></div>
  <div class="service-icon"><svg width="40" height="30"><path d="M4 26h32M8 22c2-8 4-12 6-14M16 22c0-8 2-12 4-16M24 22c0-7 2-11 5-14M32 22c0-6-1-10-3-12" stroke="#b8892b" stroke-width="1.6" fill="none"/></svg></div>
  <h3 class="service-title">Lawn Fertilizing</h3>
  <p class="service-text">Lorem Ipsum Is Simply Dummy Text Of The Printing And Typesetting Industry. Contrary Belief, Lorem Ipsum  Random Text.</p>
</article>
<article class="service-card" style="left:454px">
  <div class="service-photo" role="img" aria-label="Outdoor patio with lounge seating" style="background:linear-gradient(180deg,#c9cfc8 0%,#9aa090 50%,#6b6253 100%)"></div>
  <div class="service-icon"><svg width="36" height="34"><path d="M6 10h24M10 10v22M26 10v22M6 20h24M14 4h8v6h-8z" stroke="#b8892b" stroke-width="1.8" fill="none"/></svg></div>
  <h3 class="service-title">Patios</h3>
  <p class="service-text">Lorem Ipsum Is Simply Dummy Text Of The Printing And Typesetting Industry. Contrary Belief, Lorem Ipsum  Random Text.</p>
</article>
<article class="service-card" style="left:767px">
  <div class="service-photo" role="img" aria-label="Gardener spraying leafy plants" style="background:linear-gradient(135deg,#5e8f3c 0%,#87b04e 55%,#23346b 100%)"></div>
  <div class="service-icon"><svg width="36" height="34"><path d="M18 30V6M18 18l-10-8M18 18l10-8M18 22l-12 2M18 22l12 2" stroke="#b8892b" stroke-width="1.6" fill="none"/></svg></div>
  <h3 class="service-title">Weed Control</h3>
  <p class="service-text">Lorem Ipsum Is Simply Dummy Text Of The Printing And Typesetting Industry. Contrary Belief, Lorem Ipsum  Random Text.</p>
</article>
<a class="btn" style="left:534px;top:1125px;width:132px;height:34px">Request A Quote</a>

<section class="about">
  <h2 class="about-title">About<br><span class="accent">Brimsett Gardening</span></h2>
  <div class="about-text">
    <p>Lorem Ipsum Is Simply Dummy Text Of The Printing And Typesetting Industry. Lorem Ipsum Has Been The Industry's Standard Dummy Text Ever Since The 1500s, When An Unknown Printer Took A Galley Of Type And Scrambled It To Make A Type Specimen Book.</p>
    <p>Lorem Ipsum Is Simply Dummy Text Of The Printing And Typesetting Industry. Lorem Ipsum Has Been The Industry's Standard Dummy Text Ever Since The 1500s, When  And Scrambled It To Make A Type Specimen Book.</p>
  </div>
  <a class="btn" style="left:142px;top:376px;width:92px;height:33px">Read More</a>
  <div class="about-frame"></div>
  <div class="about-photo" role="img" aria-label="Large white house with wraparound porch behind a wide green lawn"></div>
</section>

<h2 class="heading abs" style="left:0;width:1200px;top:1834px">Customer <span class="accent">Reviews</span></h2>
<div class="review-card">
  <p class="review-text">Lorem Ipsum Is Simply Dummy Text Of The Printing And Typesetting Industry. Lorem Ipsum Has Been The Industry's Standard Dummy Text Ever Since The 1500s, When An Unknown Printer Took A Galley Of Type And Scrambled It To Make A Type Specimen Book.</p>
  <div class="review-name">– Harriet. K</div>
  <svg class="review-arrows" width="50" height="16" viewBox="0 0 50 16"><path d="M18 8H4M9 3L4 8l5 5" stroke="#111" stroke-width="1.5" fill="none"/><path d="M30 8h14M39 3l5 5-5 5" stroke="#b8892b" stroke-width="1.5" fill="none"/></svg>
</div>
<div class="quote-badge">&ldquo;</div>

<section class="band">
  <div class="band-photo" role="img" aria-label="Covered outdoor terrace with sofas and ottomans surrounded by greenery"></div>
  <div class="band-shade"></div>
  <h2 class="band-title">Build Your Outdoor Dream With Us</h2>
  <p class="band-text">Lorem Ipsum Is Simply Dummy Text Of The Printing And Typesetting Industry. Lorem Ipsum Has Been The Industry's Standard Dummy Text Ever Since The 1500s, When An Unknown Printer Took A Galley Of Type And Scrambled It To Make A Type Specimen Book.</p>
  <a class="btn" style="left:552px;top:256px;width:98px;height:33px">Contact Us</a>
</section>

<h2 class="heading abs" style="left:0;width:1200px;top:2732px">Work <span class="accent">Gallery</span></h2>
<div class="gallery-tile" role="img" aria-label="Golf course fairway lined with pine trees" style="left:142px;top:2800px;background:linear-gradient(180deg,#6d7d66 0%,#3f6a2c 45%,#7cbd3c 100%)"></div>
<div class="gallery-tile" role="img" aria-label="Hand holding a tuft of grass" style="left:454px;top:2800px;background:linear-gradient(135deg,#8fb35a 0%,#5f8f36 60%,#b59b7c 100%)"></div>
<div class="gallery-tile" role="img" aria-label="Round hay bale on a mown field" style="left:767px;top:2800px;background:linear-gradient(180deg,#6e8a3f 0%,#8a8f70 50%,#5a7a2e 100%)"></div>
<div class="gallery-tile" role="img" aria-label="Worker laying rolls of turf" style="left:142px;top:3038px;background:linear-gradient(180deg,#6f9a3d 0%,#7d6a55 55%,#5b4c3c 100%)"></div>
<div class="gallery-tile" style="left:454px;top:3038px">
  <div role="img" aria-label="Freshly landscaped lawn" style="position:absolute;inset:0;background:linear-gradient(180deg,#6b7a55 0%,#545a45 100%)"></div>
  <div class="gallery-caption">
    <h3>Lorem Ipsum  Text</h3>
    <p>Lorem Ipsum Has Been The Industry's Standard Dummy Text Ever Since The 1500s, When An  Galley Of Type And Scrambled It To Make A Type Specimen Book.</p>
  </div>
</div>
<div class="gallery-tile" role="img" aria-label="Curving brick path through a sunny park" style="left:767px;top:3038px;background:linear-gradient(180deg,#bcd6e8 0%,#4f9a35 40%,#6cb13a 70%,#b07a63 100%)"></div>
<a class="btn" style="left:552px;top:3282px;width:98px;height:33px">Contact Us</a>

<section class="inquiry">
  <h2 class="heading abs" style="left:0;width:1200px;top:86px">Quick <span class="accent">Inquiry</span></h2>
  <div class="field" style="left:290px;top:161px;width:301px;height:31px">First Name*</div>
  <div class="field" style="left:607px;top:161px;width:303px;height:31px">Last Name*</div>
  <div class="field" style="left:290px;top:207px;width:301px;height:31px">Email*</div>
  <div class="field" style="left:607px;top:207px;width:303px;height:31px">Phone Number*</div>
  <div class="field" style="left:290px;top:253px;width:620px;height:83px;padding-top:10px">Message</div>
  <a class="btn" style="left:290px;top:352px;width:620px;height:31px">Submit</a>
</section>

<footer class="footer">
  <div class="footer-brand">BRIMSETT<br>GARDENING</div>
  <div class="footer-head" style="left:413px">Quick Links</div>
  <ul class="footer-links"><li>Home</li><li>Services</li><li>Gallery</li><li>About Us</li><li>FAQs</li><li>Contact Us</li></ul>
  <div class="footer-head" style="left:615px">Contact Details</div>
  <div class="contact-row" style="left:615px;top:100px">
    <span class="icon-dot"><svg width="16" height="18"><path d="M8 17s6-6 6-10A6 6 0 0 0 2 7c0 4 6 10 6 10z" fill="none" stroke="#111" stroke-width="1.5"/><circle cx="8" cy="7" r="2" fill="#111"/></svg></span>
    <span>123, Street Name, City<br>Name, Country Name,  1234</span>
  </div>
  <div class="contact-row" style="left:615px;top:151px">
    <span class="icon-dot"><svg width="16" height="16"><path d="M4 1l3 3-2 2c1 2 3 4 5 5l2-2 3 3-2 3C7 14 2 9 1 3z" fill="#111"/></svg></span>
    <span>123 456 7890</span>
  </div>
  <div class="contact-row" style="left:615px;top:200px">
    <span class="icon-dot"><svg width="16" height="12"><rect x="1" y="1" width="14" height="10" fill="none" stroke="#111" stroke-width="1.4"/><path d="M1 1l7 6 7-6" fill="none" stroke="#111" stroke-width="1.4"/></svg></span>
    <span>hello@brimsettgardening.com</span>
  </div>
  <div class="footer-head" style="left:951px">Follow Us</div>
  <div class="social-row" style="left:951px;top:100px"><span class="icon-dot"></span><span>Community Page</span></div>
  <div class="social-row" style="left:951px;top:151px"><span class="icon-dot"></span><span>Photo Journal</span></div>
  <div class="social-row" style="left:951px;top:200px"><span class="icon-dot"></span><span>Business Profile</span></div>
</footer>
<div class="copyright">© 2024 Brimsett Gardening. All Rights Reserved.</div>

</body>
</html>
```